Copper Field Agency Website - Wordpress Web UPDATED BRIEF

FINAL LOGO UPLOADED - please look to this as reference for how we would like the site to look and feel.

We are a digital marketing agency - looking to have a new website built. We are looking for a simple one page feel of site that will allow us to grow it later. (Feel free to take some liberties with that if your imagination veers off) Must be very, playful, bold, sleek and easily integrate video. Wordpress only.

Overview:

Copper Field is a creative constellation. We are built on what's great about the shared economy. With access to thousands of content creators, designers, technicians, writers, strategists and other creatives around the world, we are built differently than a traditional “brick and mortar” Marketing Agency. We provide the traditional services our clients have come to expect, without the “5X factor” of covering the overhead common in the old agency model. We believe even better work can be created in collaboration with our clients and by passing those savings back to them for their use. Our clients pay for our art, our work and our passion –not our furniture.

"Copper Field, Let's Build Together"

Target Market(s)

companies looking for creative agency help, video production, creative consulting and coaching

Industry/Entity Type

Digital Marketing

Coding

Coded - Design and coding required

Number of Pages Required

1 page

Font styles to use
Sans Serif

Colors
3277b5
33a6d7
ec1f27

Requirements
Must have
• Wordpress design is a must. Looking for a one sheet homepage - with sections that are all on the main front page. We will have videos to embed, and should be able to have client logos and easy access to show a variety of our creative work.
• Please look to the logo for how we would like the site to feel.
• Please think "icon process flow" instead of blocks of text (which we used to have). Use the text to explain what the process flow should represent - don't actually copy paste the text but show it visually in icons.
Nice to have
• innovation around how we show video content. solid colors complementary to our palette and aesthetic.
Should not have
• Standard HTML coding

```html
<!DOCTYPE html>
<html lang="en">
<head>
<meta charset="utf-8">
<title>Copper Field Agency</title>
<link href="https://fonts.googleapis.com/css2?family=Titillium+Web:wght@300;400;600;700&display=swap" rel="stylesheet">
<style>
:root{
  --blue:#3277b5;
  --sky:#33a6d7;
  --red:#ec1f27;
  --ink:#333;
  --muted:#666;
  --light:#e6e6e6;
  --strip:#dcdcdc;
  --dark:#1f1f1f;
  --white:#fff;
}
*{margin:0;padding:0;box-sizing:border-box}
html,body{width:1200px;height:3072px;overflow:hidden}
body{font-family:"Titillium Web",Arial,sans-serif;color:var(--ink);background:var(--white);position:relative}
section,header,footer{position:absolute;left:0;width:1200px}

.hero{top:0;height:580px;background:linear-gradient(135deg,#3d4650,#6b7480 40%,#4a525c 70%,#2c333b)}
.hero-photo{position:absolute;inset:0}
.nav-bar{position:absolute;top:0;left:0;width:1200px;height:28px;background:rgba(20,20,20,.8)}
.nav{position:absolute;top:0;right:150px;display:flex}
.nav a{display:block;padding:0 20px;line-height:28px;font-size:11px;color:#ccc;text-decoration:none;text-transform:uppercase;letter-spacing:.5px}
.nav a.active{background:#111;color:var(--white)}
.brand{position:absolute;top:18px;left:84px;display:flex;align-items:center;gap:10px}
.brand-dot{width:56px;height:56px;border-radius:50%;background:var(--blue);border:3px solid var(--white)}
.brand-name{font-size:24px;font-weight:700;color:var(--white)}
.play{position:absolute;left:579px;top:279px;width:42px;height:42px}
.tagline{position:absolute;top:330px;width:100%;text-align:center;color:var(--white);font-size:30px;font-weight:300}

.clients{top:580px;height:80px;background:var(--strip);display:flex;align-items:center;justify-content:center;gap:58px}
.clients span{font-size:17px;font-weight:700;color:#444;letter-spacing:1px}

.welcome{top:660px;height:380px;text-align:center}
.section-title{font-size:34px;font-weight:400;color:var(--red)}
.welcome .section-title{margin-top:56px}
.welcome p{width:940px;margin:18px auto 0;font-size:12.5px;line-height:19px;color:var(--muted)}

.services{top:1040px;height:520px;background:linear-gradient(180deg,var(--blue),var(--sky))}
.services .section-title{color:var(--white);text-align:center;margin-top:52px}
.service-card{position:absolute;width:212px;height:148px;background:var(--white);text-align:center}
.service-card svg{margin-top:26px}
.service-card p{position:absolute;bottom:18px;width:100%;font-size:17px;color:var(--blue)}
.mascot{position:absolute;left:1060px;top:300px;width:124px;height:200px;border-radius:60px 60px 20px 20px;background:linear-gradient(180deg,#5a8fc4,#2f6aa3)}

.testimonials{top:1560px;height:390px;text-align:center}
.testimonials .section-title{margin-top:68px}
.quote{width:820px;margin:24px auto 0;background:var(--light);padding:22px 40px;font-size:19px;line-height:28px;color:#444}
.avatar{width:64px;height:64px;border-radius:50%;background:linear-gradient(135deg,#7a6a5a,#b0a090);margin:18px auto 0}
.author{margin-top:8px;font-size:12px;color:var(--blue)}
.arrow{position:absolute;width:24px;height:24px}

.gallery{top:1950px;height:470px;background:var(--light);text-align:center}
.gallery .section-title{margin-top:112px}
.gallery-photo{position:absolute;top:180px;height:205px}
.gallery-panel{position:absolute;top:180px;left:760px;width:300px;height:205px;background:rgba(40,40,40,.88);text-align:left;padding:16px 20px;color:var(--white)}
.gallery-panel h3{font-size:18px;font-weight:400}
.gallery-panel p{font-size:11px;line-height:16px;margin-top:8px;color:#ddd}

.contact{top:2420px;height:540px;background:linear-gradient(180deg,var(--sky),var(--blue));text-align:center;color:var(--white)}
.contact .section-title{color:var(--white);margin-top:48px}
.contact .intro{font-size:12px;line-height:22px;margin-top:4px}
.field{position:absolute;height:26px;background:var(--white);font-size:11px;color:#888;text-align:left;padding:0 10px;line-height:26px}
.submit{position:absolute;left:560px;top:440px;width:80px;height:26px;background:#222;color:var(--white);font-size:11px;line-height:26px}

.footer{top:2960px;height:112px;background:var(--dark);color:#aaa}
.footer-links{position:absolute;left:140px;top:30px;font-size:11px;display:flex;gap:14px}
.footer .copy{position:absolute;left:140px;top:52px;font-size:10px}
.social{position:absolute;top:28px;width:24px;height:24px;border-radius:50%;background:var(--sky)}
</style>
</head>
<body>

<header class="hero">
  <div class="hero-photo" role="img" aria-label="Dark-toned photo of a desk with laptop, charts and coffee"></div>
  <div class="nav-bar"></div>
  <nav class="nav">
    <a class="active">Home</a><a>About Us</a><a>Services</a><a>Testimonials</a><a>Gallery</a><a>Contact Us</a>
  </nav>
  <div class="brand"><span class="brand-dot"></span><span class="brand-name">Copper Field</span></div>
  <svg class="play" viewBox="0 0 42 42"><circle cx="21" cy="21" r="21" fill="#fff"/><path d="M17 13 L30 21 L17 29Z" fill="#333"/></svg>
  <h1 class="tagline">Copper Field, Let's Build Together</h1>
</header>

<section class="clients">
  <span>TIDALE</span><span>Harbeck</span><span>QUILLON</span><span>OAKLINE</span><span>lunaset</span><span>ZENNOX</span><span>RAMBLEWAY</span>
</section>

<section class="welcome">
  <h2 class="section-title">Welcome to Copper Field</h2>
  <p>Copper Field is a creative constellation. We are built on what's great about the shared economy. With access to thousands of content creators, designers, technicians, writers, strategists and other creatives around the world, we are built differently than a traditional “brick and mortar” Marketing Agency. We provide the traditional services our clients have come to expect, without the “5X factor” of covering the overhead common in the old agency model. We believe even better work can be created in collaboration with our clients and by passing those savings back to them for their use. Our clients pay for our art, our work and our passion – not our furniture.</p>
</section>

<section class="services">
  <h2 class="section-title">Services</h2>
  <div class="service-card" style="left:140px;top:112px">
    <svg width="54" height="54" viewBox="0 0 54 54" fill="none" stroke="#3277b5" stroke-width="4"><circle cx="22" cy="22" r="15"/><path d="M33 33 L49 49"/></svg>
    <p>Discovery</p></div>
  <div class="service-card" style="left:376px;top:112px">
    <svg width="54" height="54" viewBox="0 0 54 54" fill="#3277b5"><circle cx="27" cy="12" r="8"/><rect x="21" y="20" width="12" height="20"/><rect x="14" y="40" width="26" height="8"/></svg>
    <p>Strategy</p></div>
  <div class="service-card" style="left:612px;top:112px">
    <svg width="60" height="54" viewBox="0 0 60 54" fill="none" stroke="#3277b5" stroke-width="3"><rect x="20" y="4" width="20" height="14"/><rect x="4" y="36" width="16" height="12"/><rect x="22" y="36" width="16" height="12"/><rect x="40" y="36" width="16" height="12"/><path d="M30 18V28M12 36V28H48V36M30 28V36"/></svg>
    <p>Project Management</p></div>
  <div class="service-card" style="left:848px;top:112px">
    <svg width="54" height="54" viewBox="0 0 54 54" fill="none" stroke="#3277b5" stroke-width="3"><rect x="10" y="4" width="34" height="46"/><path d="M17 16H37M17 24H37M17 32H37M17 40H30"/></svg>
    <p>Content</p></div>
  <div class="service-card" style="left:140px;top:280px">
    <svg width="54" height="54" viewBox="0 0 54 54" fill="none" stroke="#3277b5" stroke-width="4"><circle cx="20" cy="22" r="10"/><circle cx="38" cy="38" r="7"/><path d="M20 6V10M20 34V38M4 22H8M32 22H36"/></svg>
    <p>Production</p></div>
  <div class="service-card" style="left:376px;top:280px">
    <svg width="54" height="54" viewBox="0 0 54 54" fill="#3277b5"><rect x="6" y="8" width="42" height="30"/><path d="M22 16L34 23L22 30Z" fill="#fff"/><rect x="20" y="40" width="14" height="8"/></svg>
    <p>Paid Media</p></div>
  <div class="service-card" style="left:612px;top:280px">
    <svg width="54" height="54" viewBox="0 0 54 54" fill="none" stroke="#3277b5" stroke-width="3"><rect x="8" y="6" width="38" height="26"/><circle cx="14" cy="42" r="5"/><circle cx="27" cy="42" r="5"/><circle cx="40" cy="42" r="5"/><path d="M14 26L22 18L30 24L40 12"/></svg>
    <p>Coaching</p></div>
  <div class="mascot" role="img" aria-label="Brand mascot illustration peeking from the side"></div>
</section>

<section class="testimonials">
  <h2 class="section-title">Testimonials</h2>
  <p class="quote">“ Seeing Copper Field in action at our casting call was amazing, they had a phenomenal pool of talent and ran the audition efficiently and very effectively. ”</p>
  <div class="avatar" role="img" aria-label="Client portrait photo"></div>
  <p class="author">Jamie Calder, Brightwater Reels</p>
  <svg class="arrow" style="left:52px;top:188px" viewBox="0 0 24 24" fill="none" stroke="#555" stroke-width="3"><path d="M16 4L8 12L16 20"/></svg>
  <svg class="arrow" style="left:1124px;top:188px" viewBox="0 0 24 24" fill="none" stroke="#555" stroke-width="3"><path d="M8 4L16 12L8 20"/></svg>
</section>

<section class="gallery">
  <h2 class="section-title">Gallery</h2>
  <div class="gallery-photo" style="left:140px;width:305px;background:linear-gradient(135deg,#c9a070,#e8d0a8,#a88058)" role="img" aria-label="Team collaborating over sticky notes"></div>
  <div class="gallery-photo" style="left:455px;width:305px;background:linear-gradient(135deg,#8a98a8,#d4d8dc,#6a7886)" role="img" aria-label="Colleagues working together at a laptop"></div>
  <div class="gallery-panel">
    <h3>Creative Generals</h3>
    <p>Our team shapes bold campaigns, crisp video and playful brand stories for clients across the globe, built with care and crafted to grow.</p>
  </div>
  <svg class="arrow" style="left:52px;top:270px" viewBox="0 0 24 24" fill="none" stroke="#555" stroke-width="3"><path d="M16 4L8 12L16 20"/></svg>
  <svg class="arrow" style="left:1124px;top:270px" viewBox="0 0 24 24" fill="none" stroke="#555" stroke-width="3"><path d="M8 4L16 12L8 20"/></svg>
</section>

<section class="contact">
  <h2 class="section-title">Contact Us</h2>
  <p class="intro">Share our story, our plans and more, we can help brands of all sizes grow with bold creative work.<br>Phone: 555 0142 0199 &nbsp;|&nbsp; Email: hello@copperfield.example</p>
  <div class="field" style="left:290px;top:188px;width:300px">Name</div>
  <div class="field" style="left:610px;top:188px;width:300px">Company Name</div>
  <div class="field" style="left:290px;top:228px;width:300px">Email</div>
  <div class="field" style="left:610px;top:228px;width:300px">Phone</div>
  <div class="field" style="left:290px;top:268px;width:620px">Service for</div>
  <div class="field" style="left:290px;top:316px;width:620px;height:96px">Message</div>
  <div class="submit">SUBMIT</div>
</section>

<footer class="footer">
  <div class="footer-links"><span>Home</span><span>About Us</span><span>Services</span><span>Testimonials</span><span>Gallery</span><span>Contact Us</span></div>
  <p class="copy">Copyright © 2024 Copper Field. All rights reserved.</p>
  <span class="social" style="left:1004px"></span>
  <span class="social" style="left:1034px"></span>
</footer>

</body>
</html>
```